UK Online Escort Directory Requires a Redesigned Email Marketing Campaign (4 emails total)

These emails should be designed as marketing emails that will be sent out to approx 10,000 potential customers on a by monthly basis. The designs should be innovative, professional designs that are capable of capturing a readers attention in the blink of an eye.

We have posted this job as our in-house design capabilities are not able to create professional email designs, we therefore require a designer to redesign our email marketing campaign (4 emails total) to a professional level.

The content of the emails will be provided, along with the 5 emails that we are currently sending and the company logo. This should give the potential designer all that they need to redesign the campaign to a professional level.

Please see attached brief for more information on what is required from each individual email.

Target Market(s)

Escorts throughout the UK

Industry/Entity Type

Escort

Font styles to use
Serif
Sans Serif

Requirements
Must have
• Instant recognition of what's being offered.
Nice to have
• Imaginative / inspirational designs.
Should not have
• Any unnecessary wording or text.

```html
<!DOCTYPE html>
<html lang="en">
<head>
<meta charset="utf-8">
<title>Velvetlist UK – Be Seen On</title>
<link rel="stylesheet" href="https://fonts.googleapis.com/css2?family=Open+Sans:wght@300;400;600&family=Oswald:wght@400;500&display=swap">
<style>
  :root {
    --rose: #d9737a;
    --panel: #f0f0f0;
    --white: #ffffff;
    --ink: #1e1e1e;
    --body: #4a4a4a;
    --muted: #8a8a8a;
    --rule: #c4c4c4;
    --divider: #e4e4e4;
    --brand: #a58fd0;
    --tagline: #5a7bc0;
    --black: #000000;
  }
  * { margin: 0; padding: 0; box-sizing: border-box; }
  html, body { width: 1014px; height: 1200px; overflow: hidden; background: var(--white); }
  body { font-family: "Open Sans", Arial, sans-serif; color: var(--ink); }

  .email { position: relative; width: 1014px; height: 1200px; background: var(--white); }
  .abs { position: absolute; }
  .center { text-align: center; }

  .header { top: 0; left: 0; width: 1014px; height: 194px; background: var(--white); }
  .brand-name { left: 0; width: 1014px; top: 36px; font-weight: 300; font-size: 96px; line-height: 106px; color: var(--brand); text-align: center; letter-spacing: -1px; white-space: nowrap; }
  .tagline { left: 46px; top: 138px; font-size: 22px; line-height: 30px; font-weight: 600; color: var(--tagline); }

  .content { top: 194px; left: 0; width: 1014px; height: 921px; background: var(--panel); }

  .ribbon { top: 194px; left: 0; width: 1014px; height: 112px; }
  .ribbon-title { top: 204px; left: 0; width: 1014px; font-family: "Oswald", "Arial Narrow", sans-serif; font-weight: 400; font-size: 34px; line-height: 48px; color: var(--white); text-align: center; }

  .site-url { top: 338px; left: 0; width: 1014px; font-size: 25px; line-height: 36px; color: var(--ink); }

  .stats { top: 426px; left: 37px; width: 940px; height: 321px; background: var(--white); }
  .stats-divider { top: 460px; left: 507px; width: 1px; height: 287px; background: var(--divider); }

  .stat-left { top: 494px; left: 37px; width: 470px; }
  .stat-right { top: 494px; left: 507px; width: 470px; padding-left: 60px; }
  .stat-lead { font-size: 25px; color: var(--body); line-height: 36px; }
  .stat-figure { font-family: "Oswald", "Arial Narrow", sans-serif; font-weight: 500; font-size: 86px; line-height: 100px; color: var(--rose); }
  .stat-note { font-size: 25px; color: var(--body); line-height: 36px; }
  .stat-example { font-size: 20px; color: var(--muted); line-height: 32px; }
  .figure-row { display: flex; align-items: baseline; justify-content: center; gap: 10px; }

  .double-rule { top: 781px; left: 37px; width: 940px; height: 9px; border-top: 2px solid var(--rule); border-bottom: 2px solid var(--rule); }

  .button { top: 843px; width: 213px; height: 56px; background: var(--black); color: var(--white); font-size: 24px; line-height: 56px; text-align: center; border-radius: 3px; }
  .button-post { left: 154px; }
  .button-contact { left: 649px; }
  .action-text { top: 910px; font-size: 25px; line-height: 37px; color: var(--ink); text-align: center; }
  .action-left { left: 0; width: 522px; }
  .action-right { left: 500px; width: 514px; }

  .signoff { top: 1021px; left: 37px; font-size: 27px; line-height: 38px; font-weight: 600; color: var(--ink); }

  .footer { top: 1115px; left: 0; width: 1014px; height: 85px; background: var(--white); }
  .copyright { top: 1142px; left: 0; width: 1014px; font-size: 21px; line-height: 30px; color: var(--muted); text-align: center; }
</style>
</head>
<body>
<main class="email">
  <header class="abs header"></header>
  <div class="abs brand-name">velvetlist-uk.com</div>
  <div class="abs tagline">The Escort Directory</div>

  <section class="abs content"></section>

  <svg class="abs ribbon" width="1014" height="112" viewBox="0 0 1014 112" aria-hidden="true">
    <path d="M0 0 H1014 V68 H560 C530 68 515 90 507 112 C499 90 484 68 454 68 H0 Z" fill="var(--rose)"/>
  </svg>
  <div class="abs ribbon-title">BE SEEN ON</div>

  <div class="abs site-url center">www.velvetlist-uk.com</div>

  <div class="abs stats"></div>
  <div class="abs stats-divider"></div>

  <div class="abs stat-left center">
    <p class="stat-lead">Your ad will be seen by</p>
    <p class="stat-figure">15,000</p>
    <p class="stat-note">customers a day</p>
  </div>

  <div class="abs stat-right center">
    <p class="stat-lead">See where we are on</p>
    <div class="figure-row">
      <span class="stat-figure">FINDLY</span>
      <span class="stat-note">type,</span>
    </div>
    <p class="stat-note">(your town + escorts)</p>
    <p class="stat-example">e.g. Birmingham escorts</p>
  </div>

  <div class="abs double-rule"></div>

  <div class="abs button button-post">Post an ad</div>
  <div class="abs button button-contact">Contact Us</div>

  <div class="abs action-text action-left">www.velvetlist-uk.com/post/ad/</div>
  <div class="abs action-text action-right">support@velvetlist-uk.com<br>for more information.</div>

  <div class="abs signoff">The VLUK Team</div>

  <footer class="abs footer"></footer>
  <div class="abs copyright">Copyright 2016 Velvetlist-uk.com All Rights Reserved</div>
</main>
</body>
</html>
```